need eczema bath soak label/bag

need you to recreate this please. ai file. recreate this exact image please. ...if you want a big tip, create some different styles.

Colors
0054AA
0677BA
7BADD7
CADEEF
E8F1F8

```html
<!DOCTYPE html>
<html lang="en">
<head>
<meta charset="utf-8">
<title>The Ocean Healed Soak – Bath Soak Label</title>
<link rel="stylesheet" href="https://fonts.googleapis.com/css2?family=Montserrat:wght@300;400;600;700;800&display=swap">
<style>
  :root {
    --ink: #0c3437;
    --paper: #ffffff;
    --sea-deep: #2fb3b3;
    --sea-light: #6fcfc8;
    --foam: #f4f7f6;
    --wet-sand: #d9cbbd;
    --sand: #ecd3a4;
    --sand-dark: #e4c691;
  }
  * { margin: 0; padding: 0; box-sizing: border-box; }
  html, body {
    width: 764px;
    height: 1200px;
    overflow: hidden;
    background: var(--paper);
  }
  .label {
    position: relative;
    width: 764px;
    height: 1200px;
    overflow: hidden;
    font-family: "Montserrat", sans-serif;
    color: var(--ink);
    background: var(--paper);
  }
  .label__scene {
    position: absolute;
    inset: 0;
    width: 764px;
    height: 1200px;
  }
  .label__text {
    position: absolute;
    left: 0;
    width: 100%;
    text-align: center;
  }
  .title-the {
    top: 248px;
    font-size: 38px;
    font-weight: 800;
    letter-spacing: 0.5px;
    line-height: 1;
  }
  .title-main {
    top: 308px;
    font-size: 96px;
    font-weight: 800;
    letter-spacing: -2px;
    line-height: 103px;
  }
  .tagline {
    top: 624px;
    font-size: 20px;
    font-weight: 400;
    line-height: 28px;
  }
  .treatment {
    top: 730px;
    font-size: 25px;
    font-weight: 700;
    letter-spacing: -0.3px;
  }
  .weight {
    top: 772px;
    font-size: 28px;
    font-weight: 600;
    letter-spacing: -0.5px;
  }
  .product-type {
    top: 824px;
    font-size: 20px;
    font-weight: 300;
  }
  .brand {
    position: absolute;
    top: 1062px;
    left: 0;
    width: 100%;
    display: flex;
    justify-content: center;
    align-items: center;
    gap: 10px;
  }
  .brand__mark {
    width: 16px;
    height: 16px;
    background: var(--ink);
  }
  .brand__name {
    font-size: 18px;
    font-weight: 800;
    letter-spacing: 5px;
    color: var(--ink);
  }
</style>
</head>
<body>
<main class="label">
  <svg class="label__scene" viewBox="0 0 764 1200" role="img" aria-label="Aerial photograph of a turquoise ocean wave washing over a sandy beach, fading into white at the top">
    <defs>
      <linearGradient id="shoreGradient" x1="0" y1="0" x2="0" y2="1">
        <stop offset="0" stop-color="#ffffff"/>
        <stop offset="0.28" stop-color="#ffffff"/>
        <stop offset="0.35" stop-color="#a9e2dc"/>
        <stop offset="0.42" stop-color="#3fbab6"/>
        <stop offset="0.50" stop-color="#35b5b2"/>
        <stop offset="0.56" stop-color="#9fd9d2"/>
        <stop offset="0.61" stop-color="#f4f7f6"/>
        <stop offset="0.66" stop-color="#f2f3f1"/>
        <stop offset="0.70" stop-color="#dccfc2"/>
        <stop offset="0.78" stop-color="#e2d3c0"/>
        <stop offset="0.82" stop-color="#ecd3a4"/>
        <stop offset="1" stop-color="#ebd1a2"/>
      </linearGradient>
    </defs>
    <rect width="764" height="1200" fill="url(#shoreGradient)"/>
  </svg>

  <p class="label__text title-the">THE</p>
  <h1 class="label__text title-main">OCEAN<br>HEALED<br>SOAK</h1>
  <p class="label__text tagline">bath soak to relieve symptoms<br>of mid eczema &amp; itchy, irritated,<br>dry skin</p>
  <p class="label__text treatment">SOOTHING TREATMENT</p>
  <p class="label__text weight">170g/6oz</p>
  <p class="label__text product-type">BATH SOAK</p>

  <div class="brand">
    <span class="brand__mark"></span>
    <span class="brand__name">SALTWAVE</span>
  </div>
</main>
</body>
</html>
```